Oil Field Service company needs professional business cards

Looking to clean up our current company business cards and look a little more professional. Brenwick Casing Services is a US based company that services the oil field. We deal with engineers, managers and oil rigs....................................................................................................................................................................................................................................................................................................................................................................................................

Target Market(s)

Oil and Gas professionals

Industry/Entity Type

Oil And Gas

Contact Information for Business Card

See attached photo as example

Font styles to use
Sans Serif

Colors
ec1f27

Requirements
Must have
• Company Logo, Name, Title, Cell, Office, Fax, Email.
• See attached photo
Nice to have
• External CRT, Internal CRT, Casing Crews, Torque Turn, Laydown Machine
Should not have
• Do not introduce any new pictures and keep it professional looking

```html
<!DOCTYPE html>
<html lang="en">
<head>
<meta charset="utf-8">
<title>Brenwick Casing Services – Business Card</title>
<link href="https://fonts.googleapis.com/css2?family=PT+Sans:wght@400;700&display=swap" rel="stylesheet">
<style>
  :root {
    --slate: #45545f;
    --red: #ec1f27;
    --ink: #4a4f55;
    --rule: #9a9da1;
    --white: #ffffff;
    --backdrop: #3b3b3b;
  }
  * { box-sizing: border-box; margin: 0; padding: 0; }
  html, body {
    width: 1105px; height: 1200px; overflow: hidden;
    background: var(--backdrop);
    font-family: "PT Sans", sans-serif;
  }
  .card {
    position: absolute; left: 196px; width: 721px; height: 411px;
    overflow: hidden;
  }
  /* Front */
  .card-front { top: 146px; background: var(--white); }
  .front-band { position: absolute; left: 0; top: 0; width: 100%; height: 66px; background: var(--slate); }
  .front-stripe { position: absolute; left: 0; bottom: 0; width: 100%; height: 12px; background: var(--red); }
  .wordmark {
    position: absolute; left: 0; width: 100%; text-align: center;
    font-weight: 700; line-height: 1;
  }
  .wordmark .name { display: block; font-size: 58px; letter-spacing: 1px; }
  .wordmark .sub { display: block; font-size: 20px; letter-spacing: 3px; margin-top: 10px; }
  .card-front .wordmark { top: 84px; color: var(--slate); }
  .rule { position: absolute; left: 35px; right: 35px; height: 1px; background: var(--rule); }
  .rule-top { top: 238px; }
  .rule-bottom { top: 367px; }
  .contact-list { position: absolute; left: 35px; top: 248px; list-style: none; }
  .contact-list li {
    display: flex; align-items: center; height: 27.5px;
    font-size: 19px; color: var(--ink);
  }
  .contact-list svg { width: 17px; height: 17px; margin-right: 10px; fill: var(--red); flex: none; }
  .person { position: absolute; right: 35px; top: 244px; text-align: right; color: var(--ink); }
  .person .person-name { font-size: 26px; font-weight: 700; color: var(--red); line-height: 32px; }
  .person .line { font-size: 19px; line-height: 27.5px; }
  .person .title { margin-bottom: 9px; }
  /* Back */
  .card-back { top: 602px; background: var(--slate); }
  .card-back .wordmark { top: 162px; color: var(--white); }
  .services {
    position: absolute; left: 0; width: 100%; top: 322px;
    text-align: center; color: var(--white); font-size: 19px; line-height: 27px;
  }
</style>
</head>
<body>
  <section class="card card-front">
    <div class="front-band"></div>
    <div class="wordmark">
      <span class="name">BRENWICK</span>
      <span class="sub">CASING SERVICES</span>
    </div>
    <div class="rule rule-top"></div>
    <ul class="contact-list">
      <li><svg viewBox="0 0 24 24" aria-hidden="true"><path d="M6.6 10.8a15.1 15.1 0 0 0 6.6 6.6l2.2-2.2a1 1 0 0 1 1-.25 11.4 11.4 0 0 0 3.6.57 1 1 0 0 1 1 1V20a1 1 0 0 1-1 1A17 17 0 0 1 3 4a1 1 0 0 1 1-1h3.5a1 1 0 0 1 1 1c0 1.25.2 2.45.57 3.57a1 1 0 0 1-.25 1z"/></svg>(555)214-6800</li>
      <li><svg viewBox="0 0 24 24" aria-hidden="true"><path d="M7 1h10a2 2 0 0 1 2 2v18a2 2 0 0 1-2 2H7a2 2 0 0 1-2-2V3a2 2 0 0 1 2-2zm0 3v14h10V4zm5 15.5a1.2 1.2 0 1 0 0 2.4 1.2 1.2 0 0 0 0-2.4z"/></svg>(555)387-1592</li>
      <li><svg viewBox="0 0 24 24" aria-hidden="true"><path d="M7 2h10v5H7zM3 9h18a2 2 0 0 1 2 2v7h-4v4H5v-4H1v-7a2 2 0 0 1 2-2zm4 8v3h10v-3z"/></svg>(555)214-6830</li>
      <li><svg viewBox="0 0 24 24" aria-hidden="true"><path d="M2 5h20v2l-10 6L2 7zm0 4.3 10 6 10-6V19H2z"/></svg>cody@brenwick.com</li>
    </ul>
    <div class="person">
      <div class="person-name">Cody Harlan</div>
      <div class="line title">Area Manager</div>
      <div class="line">Redfield, OK 73850</div>
      <div class="line">www.brenwick.com</div>
    </div>
    <div class="rule rule-bottom"></div>
    <div class="front-stripe"></div>
  </section>

  <section class="card card-back">
    <div class="wordmark">
      <span class="name">BRENWICK</span>
      <span class="sub">CASING SERVICES</span>
    </div>
    <p class="services">External CRT • Internal CRT • Casing Crews<br>Torque Turn • Laydown Machine</p>
  </section>
</body>
</html>
```